Federal IT Consulting Company - Brisolux Consulting Group

We're seeking a skilled web designer to create a modern, bold, and engaging WordPress website for Brisolux Consulting Group, LLC. Our company specializes in federal IT consulting, and our name is a play on "Brightening Solutions." The website should reflect our expertise in the federal technology marketplace and position us as a trusted partner for clients navigating their IT journey.

contact: info@brisoluxgrp-example.com

Current Status

WordPress is already installed on our hosting account
We have an existing logo (may need modernization)

Design Requirements

Style:

Modern and visually striking design
Bold elements to convey confidence and expertise
Incorporate the concept of "brightening solutions" into the design

Features:

Modern UX sliders for dynamic content presentation
Eye-catching, high-quality images (stock photos to be sourced by the designer)
Responsive design for all devices

Color Scheme:

To be proposed by the designer, should align with our brand and convey trust and technological expertise

Logo:

Evaluate our current logo
Create a transparent background version if needed
Propose modernization if deemed necessary

Accessibility:

Ensure design elements are accessible to users with disabilities
Use high contrast ratios for text and background colors
Provide text alternatives for non-text content

Website Structure
Create the following pages, with the possibility of subpages:

Home
Services
About
Contact

Specific Page Requirements
Home Page

Striking hero section with a clear value proposition
Overview of our services
Client testimonials or trust indicators

Services Page

Detailed list of our IT consulting services
Clear explanation of how we help navigate the federal IT landscape

About Page

Company history and mission
Team highlights (if applicable)
Our approach to federal IT consulting

Contact Page

Contact form
Other contact methods (phone, email)

Technical Requirements

Fully responsive design
SEO best practices implemented
Fast loading times
Integration with necessary plugins (to be discussed)
Training on how to update and maintain the site
Full compliance with Web Content Accessibility Guidelines (WCAG) 2.1 Level AA
Adherence to Section 508 standards for federal website accessibility
Implementation of necessary features for ADA compliance
Updates

Designs look the same

Target Market(s)

US Federal Govt customers looking for IT support.

Industry/Entity Type

IT Consulting

Coding

Coded - Design and coding required

Colors
0054AA
0677BA
7BADD7
CADEEF
E8F1F8
0094D4
00A9DD
6FCCEA
C7EBF8
E9F6FB
00AB8E
00BBA5
67D7C9
C6EFE9
E9F9F6

```html
<!DOCTYPE html>
<html lang="en">
<head>
<meta charset="utf-8">
<title>Brisolux Consulting Group – Federal IT Consulting</title>
<link href="https://fonts.googleapis.com/css2?family=Outfit:wght@400;500;600;700&display=swap" rel="stylesheet">
<style>
:root{
  --blue:#0054AA;
  --blue-mid:#0677BA;
  --sky:#00A9DD;
  --sky-2:#0094D4;
  --pale:#E3F4FB;
  --navy:#0B2B57;
  --navy-2:#2A4670;
  --ink:#111827;
  --muted:#4B5563;
  --white:#ffffff;
  --line:#D6E4F0;
}
*{box-sizing:border-box;margin:0;padding:0}
html,body{width:1200px;height:4155px;overflow:hidden}
body{position:relative;font-family:"Outfit",sans-serif;color:var(--ink);background:var(--white)}
.abs{position:absolute}
a{color:inherit;text-decoration:none}

.hero-band{left:0;top:0;width:1200px;height:557px;background:var(--pale)}
.brand{display:flex;align-items:center;gap:10px;font-weight:700;font-size:30px;color:var(--blue);letter-spacing:1px}
.brand-dot{width:30px;height:30px;border-radius:50%;border:5px solid var(--sky)}
.nav{top:26px;left:695px;display:flex;gap:36px;font-size:14px;font-weight:500}
.nav .active{color:var(--sky)}
.btn{display:inline-flex;align-items:center;justify-content:center;gap:8px;border-radius:24px;font-weight:600;font-size:14px}
.btn svg{width:12px;height:12px}
.btn-contact{left:950px;top:13px;width:108px;height:45px;background:var(--sky);color:var(--white);box-shadow:0 4px 12px rgba(0,169,221,.35)}
.label{font-size:12px;font-weight:500;letter-spacing:.5px;color:var(--ink);padding-left:8px;border-left:2px solid var(--ink);line-height:14px}
.label.blue{color:var(--blue-mid);border-color:var(--blue-mid)}
.label.light{color:var(--white);border-color:var(--white)}
.hero-title{left:142px;top:156px;font-size:36px;font-weight:600;line-height:47px}
.accent{color:var(--sky)}
.hero-lead{left:644px;top:195px;font-size:14px}
.btn-solid{background:var(--blue);color:var(--white)}
.btn-ghost{border:1.5px solid var(--blue);color:var(--blue);background:var(--white)}
.photo{border-radius:22px}

h2.section{font-size:28px;font-weight:600;line-height:36px}
.body-copy{font-size:12px;line-height:22.5px;color:var(--ink)}

.svc-card{width:214px;height:216px;background:var(--white);border-radius:14px;box-shadow:0 4px 24px rgba(15,40,80,.1);padding:22px}
.svc-icon{width:57px;height:56px;border-radius:8px;background:var(--blue);display:flex;align-items:center;justify-content:center}
.svc-card h3{font-size:16px;font-weight:600;margin-top:30px}
.svc-card p{font-size:12px;line-height:19.5px;margin-top:8px;width:165px}
.mini-go{position:absolute;right:12px;bottom:12px;width:28px;height:28px;border-radius:50%;background:var(--sky);display:flex;align-items:center;justify-content:center}
.round-arrow{width:38px;height:38px;border-radius:50%;display:flex;align-items:center;justify-content:center}

.testi-band{left:0;top:1878px;width:1200px;height:519px;background:var(--navy)}
.testi-card{left:258px;top:2113px;width:371px;height:223px;background:var(--white);border-radius:8px;padding:22px}
.avatar{width:56px;height:56px;border-radius:50%;background:linear-gradient(135deg,#c98b78,#7a3b35)}
.stars{position:absolute;right:22px;top:28px;display:flex;gap:3px}

.member{width:200px;text-align:center}
.member .pic{width:184px;height:184px;border-radius:50%;margin:0 auto;background:linear-gradient(180deg,#e9f3fb,#9fc8ea)}
.member h4{font-size:14px;font-weight:600;margin-top:26px}
.member .role{font-size:10px;color:var(--sky);margin-top:6px}
.socials{display:flex;justify-content:center;gap:12px;margin-top:10px}
.socials span{width:30px;height:30px;border-radius:50%;background:var(--sky);display:block}

.cta{left:142px;top:3000px;width:916px;height:328px;background:var(--blue);border-radius:40px;overflow:hidden}
.cta h2{position:absolute;left:56px;top:48px;font-size:28px;font-weight:500;color:var(--white);line-height:44px}
.cta p{position:absolute;left:56px;top:152px;font-size:13px;line-height:23px;color:var(--white);width:420px}
.cta .btn{position:absolute;left:56px;top:236px;width:190px;height:42px;background:var(--white);color:var(--blue)}

.cert{height:180px;border-radius:2px}
.footer{left:0;top:3823px;width:1200px;height:332px;background:var(--navy)}
.f-col h5{font-size:14px;font-weight:500;color:var(--sky)}
.f-col li{list-style:none;font-size:12px;color:var(--white);margin-top:13px}
.f-contact{font-size:12px;color:var(--white);display:flex;gap:12px;line-height:17px}
.f-social span{width:27px;height:27px;border-radius:50%;background:var(--sky);display:block}
</style>
</head>
<body>

<!-- Hero -->
<div class="abs hero-band"></div>
<a class="abs brand" style="left:142px;top:18px" href="#">Brisolux<span class="brand-dot"></span></a>
<nav class="abs nav"><a class="active" href="#">Home</a><a href="#">About Us</a><a href="#">Services</a></nav>
<a class="abs btn btn-contact" href="#">Contact Us</a>

<div class="abs label" style="left:142px;top:128px">WELCOME TO BRISOLUX</div>
<h1 class="abs hero-title">Navigate Your Federal<br>IT Journey with<br><span class="accent">Confidence</span>.</h1>
<p class="abs hero-lead">Expert Consulting Services to Guide Your IT Strategy.</p>
<a class="abs btn btn-solid" style="left:644px;top:253px;width:188px;height:42px" href="#">Explore Our Services
<svg viewBox="0 0 12 12" fill="none" stroke="currentColor" stroke-width="1.6"><path d="M2 10 10 2M4 2h6v6"/></svg></a>
<a class="abs btn btn-ghost" style="left:850px;top:253px;width:208px;height:42px" href="#">Get A Free Consultation
<svg viewBox="0 0 12 12" fill="none" stroke="currentColor" stroke-width="1.6"><path d="M2 10 10 2M4 2h6v6"/></svg></a>
<div class="abs photo" role="img" aria-label="Photo of a consulting team seated at a meeting table in a bright office" style="left:142px;top:344px;width:916px;height:388px;background:linear-gradient(135deg,#c9d6e0,#7e8fa0 55%,#2d4a78)"></div>

<!-- About -->
<div class="abs label blue" style="left:142px;top:859px">ABOUT US</div>
<h2 class="abs section" style="left:142px;top:885px">Why Choose <span class="accent">Brisolux?</span></h2>
<p class="abs body-copy" style="left:142px;top:945px;width:420px">There are many variations of passages of Lorem Ipsum available, but the majority have suffered alteration in some form, by injected humour, or randomised words which don't look even slightly believable. If you are going to use a passage of Lorem Ipsum, you need to be sure there isn't anything embarrassing hidden in the middle of text.</p>
<p class="abs body-copy" style="left:142px;top:1073px;width:420px">It is a long established fact that a reader will be distracted by the readable content of a page when looking at its layout.</p>
<a class="abs btn btn-solid" style="left:142px;top:1143px;width:129px;height:41px;box-shadow:0 4px 12px rgba(0,84,170,.3)" href="#">Learn More
<svg viewBox="0 0 12 12" fill="none" stroke="currentColor" stroke-width="1.6"><path d="M2 10 10 2M4 2h6v6"/></svg></a>
<div class="abs" style="left:665px;top:828px;width:385px;height:385px;border-radius:50%;border:8px solid #8a96a3;background:linear-gradient(135deg,#e2e7ec,#9aa7b5 60%,#3e5168)" role="img" aria-label="Photo of a smiling businesswoman holding a tablet, framed in a circle"></div>

<!-- Services -->
<div class="abs label blue" style="left:142px;top:1311px">POPULAR SERVICES</div>
<h2 class="abs section" style="left:142px;top:1337px">The Best Solution For<br>Your <span class="accent">Business</span></h2>
<div class="abs" role="img" aria-label="Photo of three colleagues working together at a desktop computer" style="left:0;top:1450px;width:421px;height:342px;border-radius:0 22px 22px 0;background:linear-gradient(135deg,#b89c80,#6d5a4a 50%,#2c2b30)"></div>
<div class="abs round-arrow" style="left:957px;top:1442px;border:2px solid var(--sky)"><svg width="18" height="12" viewBox="0 0 18 12" fill="none" stroke="#00A9DD" stroke-width="2"><path d="M17 6H2M6 1 1 6l5 5"/></svg></div>
<div class="abs round-arrow" style="left:1020px;top:1442px;background:var(--sky)"><svg width="18" height="12" viewBox="0 0 18 12" fill="none" stroke="#fff" stroke-width="2"><path d="M1 6h15M12 1l5 5-5 5"/></svg></div>

<div class="abs svc-card" style="left:376px;top:1513px">
  <div class="svc-icon"><svg width="30" height="30" viewBox="0 0 30 30" fill="none" stroke="#fff" stroke-width="1.6"><path d="M15 4 6 8v7c0 6 4 9 9 11 5-2 9-5 9-11V8z"/><rect x="11" y="14" width="8" height="6" rx="1"/><path d="M12.5 14v-2a2.5 2.5 0 0 1 5 0v2"/></svg></div>
  <h3>Cybersecurity</h3><p>There are many variations of passages of Lorem Ipsum available.</p>
  <span class="mini-go"><svg width="10" height="10" viewBox="0 0 12 12" fill="none" stroke="#fff" stroke-width="1.8"><path d="M2 10 10 2M4 2h6v6"/></svg></span>
</div>
<div class="abs svc-card" style="left:611px;top:1513px">
  <div class="svc-icon"><svg width="30" height="30" viewBox="0 0 30 30" fill="none" stroke="#fff" stroke-width="1.6"><path d="M9 20a6 6 0 0 1 0-12 7 7 0 0 1 13 2 5 5 0 0 1-1 10z"/><path d="M15 20v5M10 25h10"/></svg></div>
  <h3>Cloud Services</h3><p>There are many variations of passages of Lorem Ipsum available.</p>
  <span class="mini-go"><svg width="10" height="10" viewBox="0 0 12 12" fill="none" stroke="#fff" stroke-width="1.8"><path d="M2 10 10 2M4 2h6v6"/></svg></span>
</div>
<div class="abs svc-card" style="left:845px;top:1513px">
  <div class="svc-icon"><svg width="30" height="30" viewBox="0 0 30 30" fill="none" stroke="#fff" stroke-width="1.6"><rect x="6" y="5" width="18" height="12" rx="1"/><path d="M10 21h10M15 17v4M9 25h12"/><path d="M10 13l3-3 3 2 4-4"/></svg></div>
  <h3>IT Strategy Consulting</h3><p>There are many variations of passages of Lorem Ipsum available.</p>
  <span class="mini-go"><svg width="10" height="10" viewBox="0 0 12 12" fill="none" stroke="#fff" stroke-width="1.8"><path d="M2 10 10 2M4 2h6v6"/></svg></span>
</div>

<!-- Testimonials -->
<div class="abs testi-band"></div>
<div class="abs label light" style="left:142px;top:1995px">OUR TESTIMONIALS</div>
<h2 class="abs section" style="left:142px;top:2022px;color:var(--white)">Hear What Our <span class="accent">Clients Say</span></h2>
<div class="abs" style="left:868px;top:2173px;width:190px;height:167px;border-radius:14px;background:var(--navy-2)"></div>
<div class="abs" role="img" aria-label="Photo of a presenter explaining charts on a monitor to colleagues at a meeting table" style="left:600px;top:1994px;width:371px;height:256px;border-radius:10px;background:linear-gradient(135deg,#dfe6ee,#a8b8c8 50%,#5b6e86)"></div>
<svg class="abs" style="left:977px;top:2036px" width="40" height="76" viewBox="0 0 40 76" fill="#2F8FD0"><g><circle cx="2" cy="2" r="2"/><circle cx="18" cy="2" r="2"/><circle cx="34" cy="2" r="2"/><circle cx="2" cy="26" r="2"/><circle cx="18" cy="26" r="2"/><circle cx="34" cy="26" r="2"/><circle cx="2" cy="50" r="2"/><circle cx="18" cy="50" r="2"/><circle cx="34" cy="50" r="2"/><circle cx="2" cy="74" r="2"/><circle cx="18" cy="74" r="2"/><circle cx="34" cy="74" r="2"/></g></svg>
<div class="abs round-arrow" style="left:945px;top:2284px;width:36px;height:36px;border:1.5px solid var(--white)"><svg width="14" height="10" viewBox="0 0 18 12" fill="none" stroke="#fff" stroke-width="2"><path d="M17 6H2M6 1 1 6l5 5"/></svg></div>
<div class="abs round-arrow" style="left:1001px;top:2284px;width:36px;height:36px;background:var(--white)"><svg width="14" height="10" viewBox="0 0 18 12" fill="none" stroke="#0B2B57" stroke-width="2"><path d="M1 6h15M12 1l5 5-5 5"/></svg></div>
<div class="abs testi-card">
  <div class="avatar" role="img" aria-label="Client portrait"></div>
  <div class="stars" aria-label="Five star rating">
    <svg width="15" height="15" viewBox="0 0 20 20" fill="#F59E0B"><path d="M10 1l2.7 6 6.3.6-4.8 4.3 1.4 6.4L10 15l-5.6 3.3 1.4-6.4L1 7.6 7.3 7z"/></svg>
    <svg width="15" height="15" viewBox="0 0 20 20" fill="#F59E0B"><path d="M10 1l2.7 6 6.3.6-4.8 4.3 1.4 6.4L10 15l-5.6 3.3 1.4-6.4L1 7.6 7.3 7z"/></svg>
    <svg width="15" height="15" viewBox="0 0 20 20" fill="#F59E0B"><path d="M10 1l2.7 6 6.3.6-4.8 4.3 1.4 6.4L10 15l-5.6 3.3 1.4-6.4L1 7.6 7.3 7z"/></svg>
    <svg width="15" height="15" viewBox="0 0 20 20" fill="#F59E0B"><path d="M10 1l2.7 6 6.3.6-4.8 4.3 1.4 6.4L10 15l-5.6 3.3 1.4-6.4L1 7.6 7.3 7z"/></svg>
    <svg width="15" height="15" viewBox="0 0 20 20" fill="#F59E0B"><path d="M10 1l2.7 6 6.3.6-4.8 4.3 1.4 6.4L10 15l-5.6 3.3 1.4-6.4L1 7.6 7.3 7z"/></svg>
  </div>
  <div style="font-size:13px;font-weight:600;margin-top:14px">Marcus T. Ellery</div>
  <div style="font-size:10px;color:var(--muted);margin-top:6px">CEO &amp; Founder</div>
  <p style="font-size:10px;line-height:20px;color:var(--muted);margin-top:8px">It is a long established fact that a reader will be distracted by the readable content of a page when looking at its layout. The point of using Lorem Ipsum is that it has a more-or-less normal distribution.</p>
</div>

<!-- Team -->
<div class="abs label blue" style="left:562px;top:2483px">OUR TEAM</div>
<h2 class="abs section" style="left:0;width:1200px;top:2509px;text-align:center">Meet The Our <span class="accent">Experts</span></h2>
<div class="abs member" style="left:166px;top:2595px"><div class="pic" role="img" aria-label="Portrait of team member"></div><h4>Nina Calder</h4><div class="role">Web Designer</div><div class="socials"><span aria-label="Professional network profile"></span><span aria-label="Social profile"></span></div></div>
<div class="abs member" style="left:389px;top:2595px"><div class="pic" role="img" aria-label="Portrait of team member"></div><h4>Owen Prast</h4><div class="role">Web Designer</div><div class="socials"><span aria-label="Professional network profile"></span><span aria-label="Social profile"></span></div></div>
<div class="abs member" style="left:611px;top:2595px"><div class="pic" role="img" aria-label="Portrait of team member"></div><h4>Clara Venning</h4><div class="role">Web Designer</div><div class="socials"><span aria-label="Professional network profile"></span><span aria-label="Social profile"></span></div></div>
<div class="abs member" style="left:832px;top:2595px"><div class="pic" role="img" aria-label="Portrait of team member"></div><h4>Elliot Harrow</h4><div class="role">Web Designer</div><div class="socials"><span aria-label="Professional network profile"></span><span aria-label="Social profile"></span></div></div>

<!-- CTA -->
<div class="abs cta">
  <h2>We Are Federal IT Consulting<br>We Make Future!</h2>
  <p>There are many variations of passages of Lorem Ipsum available, but the majority have suffered alteration in some form.</p>
  <a class="btn" href="#">Explore Our Services
  <svg viewBox="0 0 12 12" fill="none" stroke="currentColor" stroke-width="1.6"><path d="M2 10 10 2M4 2h6v6"/></svg></a>
  <svg style="position:absolute;left:262px;top:224px" width="130" height="90" viewBox="0 0 130 90" fill="none" stroke="#9CC7EE" stroke-width="1.2"><path d="M4 86c10-30 40-10 30-40s50-10 70-24" stroke-dasharray="4 4"/><path d="M104 20l20-10-8 20-4-7z"/></svg>
</div>
<div class="abs" role="img" aria-label="Photo of a smiling consultant in a beige suit holding a laptop" style="left:677px;top:2939px;width:291px;height:389px;border-radius:140px 140px 0 0;background:linear-gradient(180deg,#e6d3bb,#c7a987 60%,#8b6a4d)"></div>

<!-- Certifications -->
<div class="abs label blue" style="left:543px;top:3416px">CERTIFICATIONS</div>
<h2 class="abs section" style="left:0;width:1200px;top:3445px;text-align:center">Certificates Of The Most<br>Popular <span class="accent">Brands</span></h2>
<div class="abs round-arrow" style="left:142px;top:3630px;width:34px;height:34px;border:1.5px solid var(--blue)"><svg width="8" height="12" viewBox="0 0 8 12" fill="none" stroke="#0054AA" stroke-width="2"><path d="M7 1 2 6l5 5"/></svg></div>
<div class="abs cert" role="img" aria-label="Certificate of achievement with ornate border" style="left:197px;top:3557px;width:253px;background:linear-gradient(135deg,#fbf3ea,#f1dcc4);border:3px solid #e7c9a5"></div>
<div class="abs cert" role="img" aria-label="Certificate with dark blue and gold corners" style="left:481px;top:3562px;width:240px;height:170px;background:linear-gradient(135deg,#1f3556 0 14%,#f1f3f6 14% 86%,#1f3556 86%)"></div>
<div class="abs cert" role="img" aria-label="Certificate of achievement with navy panel and gold seal" style="left:752px;top:3557px;width:252px;background:linear-gradient(90deg,#1b2f55 0 22%,#f4f4f6 22%)"></div>
<div class="abs round-arrow" style="left:1023px;top:3630px;width:34px;height:34px;background:var(--blue)"><svg width="8" height="12" viewBox="0 0 8 12" fill="none" stroke="#fff" stroke-width="2"><path d="M1 1l5 5-5 5"/></svg></div>

<!-- Footer -->
<footer class="abs footer">
  <a class="abs brand" style="left:142px;top:76px;font-size:40px;color:var(--white)" href="#">Brisolux<span class="brand-dot" style="width:36px;height:36px"></span></a>
  <div class="abs f-col" style="left:511px;top:73px"><h5>Quick Links</h5><ul><li>Home</li><li>About Us</li><li>Services</li></ul></div>
  <div class="abs f-col" style="left:673px;top:73px"><h5>Resources</h5><ul><li>Privacy Policy</li><li>Terms Of Service</li></ul></div>
  <div class="abs f-col" style="left:852px;top:73px"><h5>Contact Info</h5></div>
  <div class="abs f-contact" style="left:852px;top:105px"><svg width="16" height="18" viewBox="0 0 16 18" fill="#00A9DD"><path d="M8 0a6 6 0 0 0-6 6c0 5 6 11 6 11s6-6 6-11a6 6 0 0 0-6-6zm0 8.5A2.5 2.5 0 1 1 8 3.5a2.5 2.5 0 0 1 0 5z"/></svg><span>123 Lorem Ipsum Dummy, #567<br>Dummy Road 1234</span></div>
  <div class="abs f-contact" style="left:852px;top:158px"><svg width="16" height="12" viewBox="0 0 16 12" fill="#00A9DD"><path d="M0 0h16v12H0z"/><path d="M0 0l8 6 8-6" fill="none" stroke="#0B2B57" stroke-width="1.4"/></svg><span>info@brisoluxgrp-example.com</span></div>
  <div class="abs f-contact" style="left:852px;top:192px"><svg width="16" height="16" viewBox="0 0 16 16" fill="#00A9DD"><path d="M3.5 0 6 4 4.3 5.6a10 10 0 0 0 6 6L12 10l4 2.5-1 2.8C8 16 0 8 .7 1z"/></svg><span>123-456-7890</span></div>
  <div class="abs" style="left:142px;top:269px;width:916px;height:1px;background:#3A5682"></div>
  <div class="abs" style="left:142px;top:293px;font-size:12px;color:var(--white)">© 2024 Brisolux. All rights reserved.</div>
  <div class="abs f-social" style="left:909px;top:286px;display:flex;gap:13px"><span aria-label="Social profile"></span><span aria-label="Social profile"></span><span aria-label="Social profile"></span><span aria-label="Social profile"></span></div>
</footer>

</body>
</html>
```